Private Dining Restaurant Menu Design

Looking for help in designing a private dining room menu brochure - probably would need 4 panel layout to make all of the content fit, or a 5.5x8" booklet. Open to your ideas on layout/vessel - would want to post on website and be able to print to hand out to guests interested in booking our private dining room.

All content is in the attached "Private Dining Menu".

Would like to match existing dinner menu design - also attached.

Website is www.copperkettlebistro.com

Requirements
Must have
• Easy to read format of a brochure of the private dining menu content - want to be able to hand out to interested guests and have it simple and easy to read/flip through.

```html
<!DOCTYPE html>
<html lang="en">
<head>
<meta charset="utf-8">
<title>Copper Kettle Bistro – Inner Menu</title>
<link rel="stylesheet" href="https://fonts.googleapis.com/css2?family=Archivo:wght@400;600;800;900&family=Archivo+Black&display=swap">
<style>
  :root {
    --canvas: #ece6df;
    --menu-red: #c42a12;
    --menu-red-deep: #a81f0c;
    --band-yellow: #f2bd3a;
    --heading-red: #c8230f;
    --ink-light: #ffffff;
    --ink-soft: #fbe3d9;
    --photo-dark: #5a3a22;
    --photo-mid: #a9683a;
    --photo-warm: #d99a52;
  }
  * { box-sizing: border-box; margin: 0; padding: 0; }
  html, body { width: 1200px; height: 1200px; overflow: hidden; }
  body {
    background: var(--canvas);
    font-family: "Archivo", Arial, sans-serif;
    position: relative;
  }
  .menu-sheet {
    position: absolute;
    left: 215px; top: 25px;
    width: 770px; height: 1150px;
    box-shadow: 0 6px 24px rgba(0,0,0,.25);
    overflow: hidden;
  }
  .food-photo {
    position: absolute; inset: 0;
    background:
      radial-gradient(ellipse at 30% 15%, var(--photo-warm), transparent 55%),
      radial-gradient(ellipse at 75% 92%, var(--photo-warm), transparent 50%),
      linear-gradient(160deg, var(--photo-mid), var(--photo-dark) 60%, var(--photo-mid));
  }
  .menu-panel {
    position: absolute;
    left: 45px; right: 22px; top: 70px;
    background: linear-gradient(150deg, var(--menu-red), var(--menu-red-deep) 55%, var(--menu-red));
    color: var(--ink-light);
    padding-bottom: 22px;
  }
  .section-band {
    background: var(--band-yellow);
    height: 62px;
    display: flex; align-items: flex-end; justify-content: center;
    padding-bottom: 9px;
    margin-bottom: 14px;
  }
  .section-title {
    font-family: "Archivo Black", "Archivo", sans-serif;
    color: var(--heading-red);
    font-size: 30px;
    letter-spacing: .5px;
  }
  .item-list { list-style: none; padding: 0 28px 0 30px; }
  .menu-item {
    display: flex; justify-content: space-between; align-items: flex-start;
    gap: 18px;
    margin-bottom: 10px;
  }
  .item-name {
    font-weight: 900;
    font-size: 18px;
    letter-spacing: .4px;
    text-transform: uppercase;
    line-height: 1.2;
  }
  .item-desc {
    font-size: 13.5px;
    line-height: 1.3;
    color: var(--ink-soft);
  }
  .item-price {
    font-weight: 800;
    font-size: 17px;
    white-space: nowrap;
    padding-top: 1px;
  }
  .entrees { margin-top: 12px; }
  .entrees .menu-item { margin-bottom: 12px; }
</style>
</head>
<body>
  <article class="menu-sheet">
    <div class="food-photo" role="img" aria-label="Close-up photo of grilled wings, nachos and plated bar food behind the menu"></div>

    <div class="menu-panel">
      <section class="starters">
        <header class="section-band"><h2 class="section-title">STARTERS</h2></header>
        <ul class="item-list">
          <li class="menu-item"><div><h3 class="item-name">Wood-Fired Wings</h3><p class="item-desc">Buffalo, BBQ, Sweet Chili, Garlic Parmesan, Spicy Garlic, Blackened, or Signature Dry Rub.</p></div><span class="item-price">11</span></li>
          <li class="menu-item"><div><h3 class="item-name">House Made Boneless Wings</h3><p class="item-desc">Buffalo, BBQ, Sweet Chili, Garlic Parmesan, or Spicy Garlic.</p></div><span class="item-price">11</span></li>
          <li class="menu-item"><div><h3 class="item-name">Pretzel Bites</h3><p class="item-desc">Soft pretzel bites served with house cheese sauce.</p></div><span class="item-price">9</span></li>
          <li class="menu-item"><div><h3 class="item-name">Tavern Mussels</h3><p class="item-desc">One pound of mussels cooked in rich craft beer cream sauce. Served with grilled bread</p></div><span class="item-price">9</span></li>
          <li class="menu-item"><div><h3 class="item-name">Hot Artichoke Dip</h3><p class="item-desc">Served with fresh bread &amp; tortilla chips</p></div><span class="item-price">10</span></li>
          <li class="menu-item"><div><h3 class="item-name">Texas Egg Rolls</h3><p class="item-desc">House pulled pork &amp; veggies with sweet chili dipping sauce.</p></div><span class="item-price">10</span></li>
          <li class="menu-item"><div><h3 class="item-name">Wood-Roasted Quesadillas</h3><p class="item-desc">Wood-smoked chicken, pico de gallo, pickled jalapeños, cheddar &amp; jack cheeses, seasoned sour cream.</p></div><span class="item-price">9</span></li>
          <li class="menu-item"><div><h3 class="item-name">Wisconsin Cheese Curds</h3><p class="item-desc">Giant house cut cheese curds served with ranch.</p></div><span class="item-price">9</span></li>
          <li class="menu-item"><div><h3 class="item-name">Smoked Gouda Nachos</h3><p class="item-desc">Wood-roasted chicken, fire roasted corn salsa, fresh pico, pickled jalapeño &amp; lettuce with smoked gouda cheese sauce.</p></div><span class="item-price">7</span></li>
          <li class="menu-item"><div><h3 class="item-name">House Made Guacamole &amp; Chips</h3></div><span class="item-price">9</span></li>
          <li class="menu-item"><div><h3 class="item-name">Potato Skins</h3><p class="item-desc">Crisp fried potato wedges with cheese, bacon, green onions &amp; seasoned sour cream.</p></div><span class="item-price">Half 7 Full 9</span></li>
        </ul>
      </section>

      <section class="entrees">
        <header class="section-band"><h2 class="section-title">COPPER KETTLE ENTRÉES</h2></header>
        <ul class="item-list">
          <li class="menu-item"><div><h3 class="item-name">Bear Creek Pasta</h3><p class="item-desc">Angel hair pasta, wood-roasted chicken, bacon &amp; sautéed mushrooms, tossed with dijon-honey or Alfredo sauce, topped with cheddar-jack &amp; mozzarella</p></div><span class="item-price">14</span></li>
          <li class="menu-item"><div><h3 class="item-name">Wood-Grilled Sirloin</h3><p class="item-desc">Red oak-fired USDA choice Heritage Ranch Sirloin topped with roasted garlic butter, served with bacon &amp; scallion mashed potatoes &amp; charred broccoli.</p></div><span class="item-price">6 oz 15 / 9 oz 19</span></li>
          <li class="menu-item"><div><h3 class="item-name">Walleye Fish &amp; Chips</h3><p class="item-desc">Crisp breaded walleye with piping hot french fries, creamy coleslaw &amp; house walleye sauce.</p></div><span class="item-price">16</span></li>
          <li class="menu-item"><div><h3 class="item-name">Fresh Norwegian Salmon</h3><p class="item-desc">Fresh Norwegian grilled salmon topped with charred corn salsa &amp; shoestring potatoes. Served with bacon &amp; scallion mashed potatoes &amp; charred broccoli.</p></div><span class="item-price">20</span></li>
          <li class="menu-item"><div><h3 class="item-name">Wood-Grilled Ribeye</h3><p class="item-desc">14 oz corn-fed, 28 day aged, Heritage Ranch Premium Beef, red-oak grilled &amp; served with caramelized onions, loaded baked potato &amp; charred broccoli.</p></div><span class="item-price">28</span></li>
        </ul>
      </section>
    </div>
  </article>
</body>
</html>
```